RW Framewell Inc Business cards

We need business cards using our existing logo but slightly modified. Right now the logo says RW Loadbearing Masonry. We want to keep the RW part of the design, but replace the Structural Concrete portion with "FRAMEWELL". Please see the attached file.
Ideally this would be a blank template so we can add Different Names, titles, and phone numbers later.
On the one side we want only the logo and on the other side the detail. I'm attaching an example for you to see.
Please reach out with any other questions. Our address and other details will be given out once we find a design we like.

Target Market(s)

Construction Industry

```html
<!DOCTYPE html>
<html lang="en">
<head>
<meta charset="utf-8">
<title>RW Framewell Inc – Business Cards</title>
<link rel="stylesheet" href="https://fonts.googleapis.com/css2?family=Montserrat:wght@500;600&family=Open+Sans:wght@400;600&display=swap">
<style>
  :root {
    --backdrop: #e4e4e4;
    --card: #fbfbfb;
    --brand-blue: #2f5fa8;
    --brand-grey: #6b6b6b;
    --text-grey: #6f6f6f;
  }
  * { box-sizing: border-box; margin: 0; padding: 0; }
  html, body { width: 1200px; height: 852px; overflow: hidden; }
  body {
    background: var(--backdrop);
    font-family: "Open Sans", Arial, sans-serif;
    position: relative;
  }
  .card {
    position: absolute;
    top: 281px;
    width: 500px;
    height: 290px;
    background: var(--card);
    border-radius: 22px;
    overflow: hidden;
    box-shadow: 0 2px 6px rgba(0,0,0,0.12);
  }
  .card--front { left: 60px; }
  .card--back { left: 640px; }

  .edge-band {
    position: absolute;
    left: 0; right: 0; bottom: 0;
    height: 9px;
    display: flex;
  }
  .edge-band__grey { flex: 0 0 40%; background: var(--brand-grey); }
  .edge-band__blue { flex: 1; background: var(--brand-blue); }

  .wordmark {
    font-family: "Montserrat", Arial, sans-serif;
    font-weight: 600;
    color: var(--brand-blue);
    text-align: center;
    line-height: 1;
  }
  .wordmark__initials { display: block; font-size: 72px; letter-spacing: 2px; }
  .wordmark__name { display: block; font-size: 22px; letter-spacing: 7px; margin-top: 6px; }

  .card--front .wordmark {
    position: absolute;
    left: 0; right: 0; top: 88px;
  }
  .card--back .wordmark {
    position: absolute;
    left: 0; right: 0; top: 30px;
  }
  .card--back .wordmark__initials { font-size: 60px; }
  .card--back .wordmark__name { font-size: 19px; letter-spacing: 6px; }

  .person {
    position: absolute;
    left: 40px; top: 172px;
    width: 205px;
    text-align: right;
  }
  .person__name {
    font-family: "Montserrat", Arial, sans-serif;
    font-weight: 600;
    font-size: 18px;
    color: var(--brand-blue);
  }
  .person__title { font-size: 12px; color: var(--text-grey); margin-top: 2px; }
  .person__rule { height: 1.5px; background: var(--brand-blue); margin: 8px 0 7px; }
  .person__address { font-size: 12.5px; color: var(--text-grey); line-height: 1.45; }

  .contacts {
    position: absolute;
    left: 270px; top: 176px;
    list-style: none;
  }
  .contacts li {
    display: flex; align-items: center;
    font-size: 12.5px; color: var(--text-grey);
    height: 22px;
  }
  .contacts svg { width: 12px; height: 12px; margin-right: 10px; fill: var(--brand-blue); }
</style>
</head>
<body>

  <section class="card card--front" aria-label="Card front">
    <div class="wordmark">
      <span class="wordmark__initials">RW</span>
      <span class="wordmark__name">FRAMEWELL</span>
    </div>
    <div class="edge-band"><span class="edge-band__grey"></span><span class="edge-band__blue"></span></div>
  </section>

  <section class="card card--back" aria-label="Card back">
    <div class="wordmark">
      <span class="wordmark__initials">RW</span>
      <span class="wordmark__name">FRAMEWELL</span>
    </div>

    <div class="person">
      <p class="person__name">Daniel RW Hartley</p>
      <p class="person__title">Managing Director</p>
      <div class="person__rule"></div>
      <p class="person__address">78 Quarry Lane, Stonebrook,<br>California, US 90210</p>
    </div>

    <ul class="contacts">
      <li>
        <svg viewBox="0 0 24 24" aria-hidden="true"><path d="M6.6 10.8a15.1 15.1 0 0 0 6.6 6.6l2.2-2.2c.3-.3.7-.4 1-.2 1.1.4 2.3.6 3.6.6.6 0 1 .4 1 1V20c0 .6-.4 1-1 1A17 17 0 0 1 3 4c0-.6.4-1 1-1h3.5c.6 0 1 .4 1 1 0 1.3.2 2.5.6 3.6.1.3 0 .7-.2 1z"/></svg>
        555-014-2290
      </li>
      <li>
        <svg viewBox="0 0 24 24" aria-hidden="true"><path d="M2 5h20v14H2zm2 2v.5l8 5 8-5V7zm0 2.8V17h16V9.8l-8 5z"/></svg>
        dan@framewellmail.com
      </li>
      <li>
        <svg viewBox="0 0 24 24" aria-hidden="true"><circle cx="12" cy="12" r="10"/><path d="M2 12h20M12 2c3 3 3 17 0 20M12 2c-3 3-3 17 0 20" stroke="#fbfbfb" stroke-width="1.5" fill="none"/></svg>
        www.framewellco.com
      </li>
    </ul>
  </section>

</body>
</html>
```